Brimsett Gardening Fresh New Website

We are looking to create a simple fresh website for our landscaping business. The website should appeal to a 'high end' audience. We deal with a lot of Embassies and affluent clients who have extremely large gardens that are meticulously maintained. The site is about communicating our excellent landscaping and customer service skills and encouraging new clients to reach out and engage us to take care of their gardens.

The website is basically going to be our business card, it will have almost no functionality other than two 'contact us' forms, one for smaller clients and one for more detailed projects.

The website will not have a lot of written content and will have to show photos of beautifully landscaped gardens.

The main logo in black will influence the site, however, we are open to all suggestions.

We are expecting to have the following pages:
Home Page
Services
About Us
Contact Us
Showcase (photo gallery of our work)

We need someone who can code it to wordpress and be available for minor changes over a number of days. They will be simple tweaks.

```html
<!DOCTYPE html>
<html lang="en">
<head>
<meta charset="utf-8">
<title>Brimsett Gardening</title>
<link rel="stylesheet" href="https://fonts.googleapis.com/css2?family=Cinzel:wght@500;600;700&family=Lato:wght@400;700&family=Roboto:wght@400;500;700&display=swap">
<style>
:root{
  --gold:#c9962a;
  --gold-light:#e9b42a;
  --gold-dark:#a87a22;
  --ink:#1a1a1a;
  --panel:#1f1f1f;
  --text:#ffffff;
  --muted:#d8d8d8;
}
*{box-sizing:border-box;margin:0;padding:0}
html,body{width:1200px;height:3970px;overflow:hidden;background:var(--ink)}
body{position:relative;font-family:'Roboto',sans-serif;color:var(--text)}
.abs{position:absolute}
.gold-grad{background:linear-gradient(90deg,var(--gold-dark),var(--gold-light))}

/* top bar */
.topbar{left:0;top:0;width:1200px;height:48px;background:#141414;z-index:5}
.topbar-mail{left:0;top:0;width:440px;height:48px;clip-path:polygon(0 0,100% 0,88% 100%,0 100%);font-size:14px;color:#1a1a1a;padding:15px 0 0 111px}
.topbar-call{left:780px;top:15px;font-size:14px;color:#fff}
.social{display:flex;gap:7px}
.social span{width:33px;height:33px;border:2px solid var(--gold);border-radius:50%;display:flex;align-items:center;justify-content:center}
.social span::after{content:"";width:7px;height:7px;background:#fff;border-radius:50%}
.topbar .social{position:absolute;left:977px;top:7px}

/* header */
.header{left:0;top:48px;width:1200px;height:135px;background:var(--ink);z-index:5}
.brand{left:111px;top:40px;font-family:'Cinzel',serif;color:var(--gold);display:flex;align-items:center;gap:12px}
.brand-dot{width:16px;height:16px;border-radius:50%;background:var(--gold)}
.brand-name{font-size:20px;font-weight:600;letter-spacing:3px;line-height:1.2}
.brand-name small{display:block;font-size:11px;letter-spacing:6px}
.nav{left:396px;top:60px;display:flex;gap:36px;font-family:'Lato',sans-serif;font-weight:700;font-size:15px;color:#fff}
.nav .active{color:var(--gold-light)}
.btn{display:inline-block;font-family:'Lato',sans-serif;font-size:15px;color:#1a1a1a;text-align:center}
.quote-btn{left:946px;top:46px;width:142px;height:48px;line-height:48px}

/* hero */
.hero-art{left:0;top:0;width:1200px;height:1204px}
.hero-copy{left:0;top:437px;width:1200px;text-align:center}
.hero-copy h3{font-family:'Cinzel',serif;font-weight:500;font-size:23px}
.hero-copy h1{font-family:'Cinzel',serif;font-weight:600;font-size:47px;margin-top:2px}
.hero-copy p{font-family:'Lato',sans-serif;font-size:20px;line-height:31px;margin-top:8px}
.hero-btn{left:529px;top:615px;width:142px;height:48px;line-height:48px}

/* schedule */
.sec-title{font-family:'Cinzel',serif;font-weight:600;font-size:36px;text-align:center;width:1200px;left:0}
.sched-title{top:928px;color:#1a1a1a}
.field{height:50px;border:1.5px solid #3a2a0c;font-size:13px;color:#1a1a1a;padding:17px 0 0 16px;width:225px}
.submit{background:#141414;color:#fff;font-weight:500;text-align:center;padding:17px 0 0;font-size:15px}

/* about */
.photo{display:block}
.about-title{left:671px;top:1346px;font-family:'Cinzel',serif;font-weight:600;font-size:36px}
.rule{height:3px;width:82px;background:var(--gold)}
.about-text{left:671px;top:1434px;width:417px;font-size:15px;line-height:25.7px;color:var(--muted);text-align:justify}
.about-text p+p{margin-top:13px}
.learn-btn{left:671px;top:1685px;width:142px;height:48px;line-height:48px}

/* services */
.services-intro{left:160px;top:1948px;width:880px;text-align:center;font-size:15px;line-height:26px;color:var(--muted)}
.svc-label{top:2478px;font-weight:700;font-size:18px;letter-spacing:.3px}

/* gallery */
.gallery{left:0;top:2623px;width:1200px;height:1347px;background:var(--panel)}
.gal{position:absolute}

/* footer */
.f-title{font-weight:700;font-size:18px}
.links{left:111px;top:3622px;list-style:none;font-size:14px;line-height:34.3px}
.links li::before{content:"»";color:var(--gold);margin-right:22px}
.contact-item{left:317px;display:flex;gap:23px}
.ic{width:36px;height:36px;background:#fff;display:flex;align-items:center;justify-content:center;flex:none}
.contact-item b{display:block;font-size:14px;font-weight:700;margin-bottom:4px}
.contact-item span{font-size:12px;line-height:20px;color:var(--muted)}
.in{position:absolute;height:48px;border:1px solid #555;font-size:14px;color:#ddd;padding:15px 0 0 16px}
.send-btn{left:627px;top:3833px;width:160px;height:49px;line-height:49px}
.bottom-rule{left:111px;top:3907px;width:978px;height:1px;background:#3b3b3b}
.copy{left:0;top:3928px;width:1200px;text-align:center;font-size:12px;color:#ddd}
.footer-social{left:977px;top:3919px}
</style>
</head>
<body>

<!-- hero + schedule band -->
<svg class="abs hero-art" viewBox="0 0 1200 1204" width="1200" height="1204">
  <defs>
    <linearGradient id="garden" x1="0" y1="0" x2="0" y2="1">
      <stop offset="0" stop-color="#1f2a16"/><stop offset=".5" stop-color="#3e5a22"/><stop offset="1" stop-color="#5a7a2a"/>
    </linearGradient>
    <linearGradient id="goldband" x1="0" y1="0" x2="1" y2="1">
      <stop offset="0" stop-color="#a87a22"/><stop offset=".6" stop-color="#d9a528"/><stop offset="1" stop-color="#ebb62a"/>
    </linearGradient>
  </defs>
  <rect x="0" y="0" width="1200" height="1204" fill="#1a1a1a"/>
  <g role="img" aria-label="Photo of a lit garden path at dusk lined with lawn, trees and shrubs">
    <polygon points="0,183 1200,183 1200,700 600,820 0,700" fill="url(#garden)"/>
  </g>
  <polygon points="0,698 600,850 1200,698 1200,1204 0,1204" fill="url(#goldband)"/>
  <polygon points="0,690 600,818 1200,690 1200,710 600,850 0,710" fill="#1f1f1f"/>
</svg>

<!-- top bar -->
<div class="abs topbar">
  <div class="abs topbar-mail gold-grad">Email Us: info@brimsettgardening.com</div>
  <div class="abs topbar-call">Call Us: +1 (555) 014 2290</div>
  <div class="social"><span></span><span></span><span></span></div>
</div>

<!-- header -->
<header class="abs header">
  <div class="abs brand"><div class="brand-dot"></div><div class="brand-name">BRIMSETT<small>GARDENING</small></div></div>
  <nav class="abs nav"><span class="active">HOME</span><span>SERVICES</span><span>ABOUT US</span><span>GALLERY</span><span>CONTACT US</span></nav>
  <div class="abs btn quote-btn gold-grad">GET A QUOTE</div>
</header>

<div class="abs hero-copy">
  <h3>WELCOME TO</h3>
  <h1>BRIMSETT GARDENING</h1>
  <p>Lorem ipsum dolor sit amet, consectetur adipiscing elit, sed do<br>eiusmod tempor incididunt laborea.</p>
</div>
<div class="abs btn hero-btn gold-grad">GET STARTED</div>

<h2 class="abs sec-title sched-title">SCHEDULE A SERVICE NOW</h2>
<div class="abs field" style="left:137px;top:1023px">Your Name</div>
<div class="abs field" style="left:371px;top:1023px">Phone</div>
<div class="abs field" style="left:605px;top:1023px">Email</div>
<div class="abs field" style="left:839px;top:1023px">Place</div>
<div class="abs field" style="left:137px;top:1084px">Select Service<svg class="abs" style="right:14px;top:21px" width="9" height="6" viewBox="0 0 9 6"><path d="M1 1l3.5 3.5L8 1" stroke="#1a1a1a" stroke-width="1.5" fill="none"/></svg></div>
<div class="abs field" style="left:371px;top:1084px">Date<svg class="abs" style="right:14px;top:17px" width="12" height="12" viewBox="0 0 12 12"><rect x="1" y="2" width="10" height="9" fill="none" stroke="#1a1a1a" stroke-width="1.3"/><rect x="1" y="2" width="10" height="3" fill="#1a1a1a"/></svg></div>
<div class="abs field" style="left:605px;top:1084px">Time<svg class="abs" style="right:14px;top:17px" width="12" height="12" viewBox="0 0 12 12"><circle cx="6" cy="6" r="5" fill="none" stroke="#1a1a1a" stroke-width="1.3"/><path d="M6 3v3h2" stroke="#1a1a1a" stroke-width="1.3" fill="none"/></svg></div>
<div class="abs field submit" style="left:839px;top:1084px;border-color:#141414">SUBMIT NOW</div>

<!-- about -->
<div class="abs photo" role="img" aria-label="Gardener planting flowers in a bed" style="left:302px;top:1331px;width:305px;height:234px;background:linear-gradient(135deg,#6f8f3a,#3c5a22 60%,#2a8ab0)"></div>
<div class="abs photo" role="img" aria-label="Hands trimming a hedge with shears" style="left:109px;top:1449px;width:279px;height:196px;background:linear-gradient(160deg,#9bb86a,#4f7a22 55%,#2c4a14);border:solid var(--ink);border-width:0 10px 10px 0"></div>
<div class="abs photo" role="img" aria-label="House with landscaped garden and pond" style="left:276px;top:1554px;width:266px;height:202px;background:linear-gradient(180deg,#d9e8f2,#8aa86a 45%,#3f7a2a);outline:10px solid var(--ink)"></div>
<h2 class="abs about-title">ABOUT US</h2>
<div class="abs rule" style="left:671px;top:1396px"></div>
<div class="abs about-text">
  <p>Lorem ipsum dolor sit amet, consectetur adipiscing elit, sed do eiusmod tempor incididunt ut labore et dolore magna aliqua. Ut enim ad minim veniam, quis nostrud exercitation ullamco laboris nisi ut aliquip ex ea commodo consequat duis aute irure dolor in reprehea.</p>
  <p>Lorem ipsum dolor sit amet, consectetur adipiscing elit, sed do eiusmod tempor incididunt ut labore et dolore magna aliqua ut enim ad minim veniam quisea.</p>
</div>
<div class="abs btn learn-btn gold-grad">LEARN MORE</div>

<!-- services -->
<h2 class="abs sec-title" style="top:1868px">OUR SERVICES</h2>
<div class="abs rule" style="left:559px;top:1918px"></div>
<p class="abs services-intro">Lorem ipsum dolor sit amet, consectetur adipiscing elit, sed do tempor incididunt ut labore et dolore magna minim veniam,<br>quis nostrud exercitation ullamco laboris nisi ut aliquipea.</p>
<svg class="abs" style="left:0;top:2036px" width="1200" height="410" viewBox="0 0 1200 410">
  <defs>
    <linearGradient id="s1" x1="0" y1="0" x2="0" y2="1"><stop offset="0" stop-color="#8aa83a"/><stop offset="1" stop-color="#3a5a1c"/></linearGradient>
    <linearGradient id="s2" x1="0" y1="0" x2="0" y2="1"><stop offset="0" stop-color="#a8b84a"/><stop offset="1" stop-color="#4a7420"/></linearGradient>
    <linearGradient id="s3" x1="0" y1="0" x2="0" y2="1"><stop offset="0" stop-color="#b8a890"/><stop offset="1" stop-color="#6a5a48"/></linearGradient>
    <linearGradient id="s4" x1="0" y1="0" x2="0" y2="1"><stop offset="0" stop-color="#6a9a3a"/><stop offset="1" stop-color="#8a8a80"/></linearGradient>
  </defs>
  <rect width="1200" height="410" fill="#1a1a1a"/>
  <g role="img" aria-label="Gardener kneeling to plant shrubs"><polygon points="0,0 318,0 260,410 0,410" fill="url(#s1)"/></g>
  <g role="img" aria-label="Gardener trimming bushes"><polygon points="332,0 620,0 562,410 274,410" fill="url(#s2)"/></g>
  <g role="img" aria-label="Laying turf beside a gravel path"><polygon points="634,0 922,0 864,410 576,410" fill="url(#s3)"/></g>
  <g role="img" aria-label="Aerial view of a gardener on a lawn with gravel beds"><polygon points="936,0 1200,0 1200,410 878,410" fill="url(#s4)"/></g>
</svg>
<div class="abs svc-label" style="left:43px">LOREM IPSUM DOL</div>
<div class="abs svc-label" style="left:334px">LOREM IPSUM DOL</div>
<div class="abs svc-label" style="left:636px">LOREM IPSUM DOL</div>
<div class="abs svc-label" style="left:952px">LOREM IPSUM DOL</div>

<!-- gallery + footer -->
<section class="abs gallery">
  <h2 class="abs sec-title" style="top:74px">OUR GALLERY</h2>
  <div class="abs rule" style="left:559px;top:124px"></div>
  <div class="gal" role="img" aria-label="Aerial view of a winding garden path through lawn" style="left:111px;top:177px;width:480px;height:282px;background:linear-gradient(135deg,#4f7a22,#8aa83a 50%,#3a5a1c)"></div>
  <div class="gal" role="img" aria-label="Curved paved path across a wide lawn" style="left:608px;top:177px;width:481px;height:282px;background:linear-gradient(180deg,#7a9a4a,#5a8a2a 55%,#8a8a88)"></div>
  <div class="gal" role="img" aria-label="Terraced flower beds with stone edging" style="left:111px;top:474px;width:316px;height:231px;background:linear-gradient(180deg,#3a5a2a,#7aa03a 60%,#b8a888)"></div>
  <div class="gal" role="img" aria-label="Stepping stone path through bamboo and pebbles" style="left:442px;top:474px;width:316px;height:231px;background:linear-gradient(180deg,#3a6a22,#7a9a4a 50%,#9a9a90)"></div>
  <div class="gal" role="img" aria-label="Back garden lawn beside a house" style="left:773px;top:474px;width:316px;height:231px;background:linear-gradient(180deg,#b8d8ee,#8aa85a 50%,#4f8a2a)"></div>

  <svg class="abs" style="left:0;top:787px" width="1200" height="160" viewBox="0 0 1200 160">
    <defs><linearGradient id="fg" x1="0" y1="0" x2="1" y2="0"><stop offset="0" stop-color="#a87a22"/><stop offset="1" stop-color="#ebb62a"/></linearGradient></defs>
    <polygon points="0,157 600,3 1200,157 600,24" fill="url(#fg)"/>
  </svg>

  <h4 class="abs f-title" style="left:111px;top:952px">QUICK LINKS</h4>
  <h4 class="abs f-title" style="left:317px;top:952px">CONTACT US</h4>
  <h4 class="abs f-title" style="left:625px;top:952px">GET IN TOUCH</h4>
</section>

<ul class="abs links">
  <li>HOME</li><li>SERVICES</li><li>ABOUT US</li><li>GALLERY</li><li>CONTACT US</li><li>PRIVACY POLICY</li><li>TERMS OF USE</li>
</ul>

<div class="abs contact-item" style="top:3627px">
  <div class="ic"><svg width="14" height="18" viewBox="0 0 14 18"><path d="M7 0a7 7 0 0 0-7 7c0 5 7 11 7 11s7-6 7-11a7 7 0 0 0-7-7z" fill="#c9962a"/><circle cx="7" cy="7" r="2.5" fill="#fff"/></svg></div>
  <div><b>LOCATION:</b><span>465, Lorum Ipsum Dolore Sed Amet,<br>United States</span></div>
</div>
<div class="abs contact-item" style="top:3716px">
  <div class="ic"><svg width="16" height="16" viewBox="0 0 16 16"><path d="M3 1l3 3-2 2c1 2 3 4 6 6l2-2 3 3-2 3C7 15 1 9 0 3z" fill="#c9962a"/></svg></div>
  <div><b>PHONE:</b><span>+1 (555) 014 2290</span></div>
</div>
<div class="abs contact-item" style="top:3806px">
  <div class="ic"><svg width="16" height="12" viewBox="0 0 16 12"><rect width="16" height="12" fill="#c9962a"/><path d="M0 0l8 6 8-6" stroke="#fff" stroke-width="1.5" fill="none"/></svg></div>
  <div><b>EMAIL:</b><span>info@brimsettgardening.com</span></div>
</div>

<div class="in" style="left:627px;top:3626px;width:226px">First Name</div>
<div class="in" style="left:861px;top:3626px;width:228px">Last Name</div>
<div class="in" style="left:627px;top:3682px;width:226px">Email Address</div>
<div class="in" style="left:861px;top:3682px;width:228px">Phone Number</div>
<div class="in" style="left:627px;top:3736px;width:462px;height:83px">Message</div>
<div class="abs btn send-btn gold-grad">SEND MESSAGE</div>

<div class="abs bottom-rule"></div>
<div class="abs copy">© 2024 <b>BRIMSETT GARDENING</b> &nbsp;| &nbsp;All Rights Reserved</div>
<div class="abs social footer-social"><span></span><span></span><span></span></div>

</body>
</html>
```